Laser Tattoo Removal Business Cards

We are looking for a professional business card design for a laser tattoo removal business. Ideally looking for a black business card design. The name of the business is Brightline Tattoo Removal. We place our cards at local tattoo shops so we ideally are looking for something trendy/edgy to draw both male and female clientele in.

Target Market(s)

Male/Female ages 18-60

Contact Information for Business Card

black background ideally.. hoping to stay within greys, whites and black

Font styles to use
Serif
Sans Serif

Colors
121212
a9a9a9
5c5c5c
f5f5f5
ffffff
7f7f7f
606060
848484
9d9d9d

Requirements
Must have
• Employee Info:
• Melissa Thornbury
• Chief Executive Offer
• m: 919.537.2846
• w: 919.362.4178
• f: 919.685.3907
• mthornbury@brightlinetattooremoval.example
• Address:
• 4615 Oakmere Pkwy, Suite 210
• Raleigh, NC 27654
• Website:
• www.brightlinetattooremoval.example
Nice to have
• Myabe business name on back or logo on back and employee info on the front

```html
<!DOCTYPE html>
<html lang="en">
<head>
<meta charset="utf-8">
<title>Brightline Tattoo Removal — Business Cards</title>
<link rel="stylesheet" href="https://fonts.googleapis.com/css2?family=Josefin+Sans:wght@300;400&family=Lato:wght@400;700&display=swap">
<style>
  :root {
    --ink: #121212;
    --charcoal: #2a2a2a;
    --mid-grey: #5c5c5c;
    --grey: #7f7f7f;
    --light-grey: #a9a9a9;
    --paper: #ffffff;
    --off-white: #f5f5f5;
    --stage: #1c1c1c;
  }
  * { box-sizing: border-box; margin: 0; padding: 0; }
  html, body { width: 1200px; height: 900px; overflow: hidden; }
  body {
    background: var(--stage);
    font-family: "Lato", sans-serif;
    position: relative;
  }
  .card {
    position: absolute;
    left: 280px;
    width: 640px;
    height: 366px;
    overflow: hidden;
    box-shadow: 0 10px 30px rgba(0,0,0,.55);
  }

  /* Back of card */
  .card-back {
    top: 50px;
    background: var(--charcoal);
    display: flex;
    flex-direction: column;
    align-items: center;
    justify-content: center;
  }
  .wordmark {
    font-family: "Josefin Sans", sans-serif;
    font-weight: 300;
    text-transform: uppercase;
    letter-spacing: 0.16em;
    text-align: center;
    line-height: 1.15;
  }
  .card-back .wordmark { color: var(--off-white); font-size: 44px; }
  .wordmark .sub { display: block; font-size: 0.42em; letter-spacing: 0.34em; margin-top: 10px; }
  .website {
    margin-top: 54px;
    color: var(--off-white);
    font-weight: 700;
    font-size: 14px;
    letter-spacing: 0.22em;
  }

  /* Front of card */
  .card-front {
    top: 484px;
    background: var(--paper);
  }
  .card-front .wordmark {
    position: absolute;
    right: 46px;
    top: 40px;
    color: var(--ink);
    font-size: 38px;
  }
  .employee {
    position: absolute;
    left: 40px;
    top: 58px;
    color: var(--ink);
  }
  .employee-name { font-size: 16px; font-weight: 400; }
  .employee-name strong { font-weight: 700; }
  .employee-title { font-size: 12px; margin-top: 2px; }
  .address {
    position: absolute;
    right: 46px;
    top: 162px;
    padding-right: 16px;
    border-right: 3px solid var(--ink);
    text-align: right;
    font-size: 13px;
    font-weight: 700;
    line-height: 1.45;
    color: var(--ink);
  }
  .edge-band { position: absolute; inset: 0; pointer-events: none; }
  .contact-tab {
    position: absolute;
    left: 0;
    bottom: 0;
    width: 44px;
    height: 152px;
    background: var(--ink);
    border-top-right-radius: 12px;
    display: flex;
    flex-direction: column;
    justify-content: space-evenly;
    align-items: center;
    padding: 10px 0;
  }
  .contact-tab svg { width: 16px; height: 16px; fill: var(--paper); }
  .contact-list {
    position: absolute;
    left: 62px;
    bottom: 14px;
    list-style: none;
    font-size: 15px;
    color: var(--ink);
    line-height: 1.7;
    height: 152px;
    display: flex;
    flex-direction: column;
    justify-content: space-evenly;
  }
</style>
</head>
<body>

<section class="card card-back">
  <div class="wordmark">Brightline<span class="sub">Tattoo Removal</span></div>
  <div class="website">www.brightlinetattooremoval.example</div>
</section>

<section class="card card-front">
  <svg class="edge-band" viewBox="0 0 640 366" aria-hidden="true">
    <path d="M640 196 L640 366 L0 366 L0 356 L520 356 Q540 356 544 330 Q548 306 580 304 L610 300 Q630 298 640 196 Z" fill="#121212"/>
    <rect x="0" y="356" width="640" height="10" fill="#7f7f7f"/>
  </svg>

  <div class="wordmark">Brightline<span class="sub">Tattoo Removal</span></div>

  <div class="employee">
    <div class="employee-name">Melissa <strong>Thornbury</strong></div>
    <div class="employee-title">Chief Executive Offer</div>
  </div>

  <div class="address">4615 Oakmere Pkwy, Suite 210<br>Raleigh, NC 27654</div>

  <div class="contact-tab">
    <svg viewBox="0 0 16 16" aria-label="Phone"><path d="M2 6c0-2 3-4 6-4s6 2 6 4v1h-3V5.5C10 5 9 4.8 8 4.8S6 5 5 5.5V7H2zM3 8h10l1 6H2z"/></svg>
    <svg viewBox="0 0 16 16" aria-label="Mobile"><path d="M4 1.5l3 3-1.6 1.6a8 8 0 004.5 4.5L11.5 9l3 3-2 2C7 14 2 9 2 3.5z"/></svg>
    <svg viewBox="0 0 16 16" aria-label="Fax"><path d="M4 1h8v4H4zM1 6h14v7h-3v2H4v-2H1zm4 4v4h6v-4z"/></svg>
    <svg viewBox="0 0 16 16" aria-label="Email"><path d="M1 3h14v10H1zm1.5 1.2L8 8.5l5.5-4.3z"/></svg>
  </div>

  <ul class="contact-list">
    <li>919.537.2846</li>
    <li>919.362.4178</li>
    <li>919.685.3907</li>
    <li>mthornbury@brightlinetattooremoval.example</li>
  </ul>
</section>

</body>
</html>
```